Tech business card design

We need an amazing business card design for our new business 'Pexla' a marketing tech startup based in Sydney, Australia. We provide an online marketplace for businesses to search and buy advertising media, connect with service providers and learn more about marketing. We wish to communicate 'cool tech', reliability and professionalism and design based around our logo.

Target Market(s)

Business Owners

Contact Information for Business Card

Name
Position
Email Address
Website
Phone Number

Font styles to use
Other font styles liked:
• Avenir & Avenir Next

Colors

Designer to choose colors to be used in the design.

```html
<!DOCTYPE html>
<html lang="en">
<head>
<meta charset="utf-8">
<title>Pexla Business Card</title>
<link href="https://fonts.googleapis.com/css2?family=Mulish:wght@300;400;700;800&display=swap" rel="stylesheet">
<style>
  :root {
    --navy: #14164f;
    --navy-deep: #0b0c33;
    --navy-light: #262a78;
    --white: #ffffff;
    --ink-grey: #6d6d74;
    --rule-grey: #8a8a90;
    --stage: #2b2b2d;
  }
  html, body {
    margin: 0;
    padding: 0;
    width: 1200px;
    height: 892px;
    overflow: hidden;
    background: var(--stage);
    font-family: "Mulish", "Avenir Next", Arial, sans-serif;
  }
  .canvas {
    position: relative;
    width: 1200px;
    height: 892px;
  }
  .card {
    position: absolute;
    width: 540px;
    height: 310px;
    border-radius: 2px;
    overflow: hidden;
    box-shadow: 0 14px 30px rgba(0,0,0,0.45);
  }
  /* Front */
  .card-front {
    left: 90px;
    top: 110px;
    background: radial-gradient(ellipse at 50% 35%, var(--navy-light) 0%, var(--navy) 45%, var(--navy-deep) 100%);
    color: var(--white);
  }
  .card-front .brand {
    position: absolute;
    left: 0;
    right: 0;
    top: 92px;
    text-align: center;
    font-weight: 800;
    font-size: 96px;
    letter-spacing: -2px;
    line-height: 1;
  }
  .card-front .web {
    position: absolute;
    left: 0;
    right: 0;
    top: 232px;
    text-align: center;
    font-weight: 400;
    font-size: 12px;
    letter-spacing: 7px;
  }
  /* Back */
  .card-back {
    left: 570px;
    top: 460px;
    background: var(--white);
    color: var(--navy);
  }
  .card-back .brand {
    position: absolute;
    left: 40px;
    top: 58px;
    font-weight: 800;
    font-size: 80px;
    letter-spacing: -2px;
    line-height: 1;
    color: var(--navy);
  }
  .card-back .identity {
    position: absolute;
    right: 30px;
    top: 36px;
    text-align: right;
  }
  .card-back .person {
    font-weight: 800;
    font-size: 19px;
    line-height: 1.1;
  }
  .card-back .role {
    font-weight: 300;
    font-size: 13px;
    color: var(--ink-grey);
    margin-top: 2px;
  }
  .card-back .corner-mark {
    position: absolute;
    right: 0;
    top: 30px;
    width: 18px;
    height: 20px;
    background: var(--navy);
  }
  .card-back .rule {
    position: absolute;
    left: 28px;
    right: 30px;
    top: 196px;
    height: 1px;
    background: var(--rule-grey);
  }
  .card-back .contacts {
    position: absolute;
    left: 30px;
    top: 208px;
    list-style: none;
    margin: 0;
    padding: 0;
    font-weight: 300;
    font-size: 14px;
    color: var(--ink-grey);
  }
  .card-back .contacts li {
    display: flex;
    align-items: center;
    gap: 10px;
    height: 22px;
  }
  .card-back .contacts svg {
    width: 14px;
    height: 14px;
    flex: none;
  }
  .card-back .web-band {
    position: absolute;
    right: 0;
    bottom: 28px;
    width: 240px;
    height: 36px;
  }
  .card-back .web-band svg {
    position: absolute;
    inset: 0;
  }
  .card-back .web-band span {
    position: absolute;
    right: 22px;
    top: 9px;
    font-size: 14px;
    font-weight: 400;
    color: var(--white);
    letter-spacing: 0.5px;
  }
</style>
</head>
<body>
<main class="canvas">
  <section class="card card-front" aria-label="Card front">
    <div class="brand">Pexla</div>
    <div class="web">www.pexlamedia.com.au</div>
  </section>

  <section class="card card-back" aria-label="Card back">
    <div class="brand">Pexla</div>
    <div class="corner-mark"></div>
    <div class="identity">
      <div class="person">Marcus Reid</div>
      <div class="role">Founder, Director</div>
    </div>
    <div class="rule"></div>
    <ul class="contacts">
      <li>
        <svg viewBox="0 0 14 14" aria-hidden="true"><rect x="3.5" y="0.8" width="7" height="12.4" rx="1.2" fill="none" stroke="#14164f" stroke-width="1.4"/><circle cx="7" cy="11" r="0.8" fill="#14164f"/></svg>
        +61 (0)412 555 208
      </li>
      <li>
        <svg viewBox="0 0 14 14" aria-hidden="true"><rect x="0.8" y="3" width="12.4" height="8.5" fill="#14164f"/><path d="M0.8 3 L7 8 L13.2 3" fill="none" stroke="#fff" stroke-width="1"/></svg>
        marcus@pexlamedia.com.au
      </li>
    </ul>
    <div class="web-band">
      <svg viewBox="0 0 240 36" width="240" height="36" aria-hidden="true"><polygon points="14,0 240,0 240,36 0,36" fill="#14164f"/></svg>
      <span>www.pexlamedia.com.au</span>
    </div>
  </section>
</main>
</body>
</html>
```